Book for new dads needs a cover.

We need a cover for a book titled Roadmap to Early Parenthood: Practical Methods for Welcoming a Newborn, Juggling Career and Home Life, and Managing Mental Health on the Path to Becoming a Parent. We would like to see a design that emphasizes healthy babies and confident dads.

```html
<!DOCTYPE html>
<html lang="en">
<head>
<meta charset="utf-8">
<title>Roadmap to Early Parenthood – Book Cover</title>
<link href="https://fonts.googleapis.com/css2?family=Bebas+Neue&family=Montserrat:wght@500;600&family=Oswald:wght@500;600&display=swap" rel="stylesheet">
<style>
  :root {
    --page: #ffffff;
    --cover-teal: #5cc5cf;
    --title-yellow: #f6ef22;
    --band-yellow: #fbf31a;
    --ink-white: #ffffff;
    --ink-dark: #1f2a44;
    --art-blue: #3a9be8;
    --art-purple: #7c3aa8;
    --art-pink: #e8639a;
  }
  * { margin: 0; padding: 0; box-sizing: border-box; }
  html, body {
    width: 1200px; height: 1000px; overflow: hidden;
    background: var(--page);
  }
  .cover {
    position: absolute; left: 268px; top: 0;
    width: 665px; height: 1000px;
    background: var(--cover-teal);
    overflow: hidden;
  }
  .author {
    position: absolute; top: 36px; left: 0; width: 100%;
    text-align: center;
    font-family: "Montserrat", sans-serif; font-weight: 600;
    font-size: 42px; letter-spacing: 9px;
    color: var(--ink-white);
  }
  .title {
    position: absolute; top: 92px; left: 0; width: 100%; height: 680px;
    z-index: 2;
    font-family: "Bebas Neue", sans-serif; font-weight: 400;
    color: var(--title-yellow);
    line-height: 0.86;
  }
  .title span {
    position: absolute; left: 0; width: 100%;
    text-align: center; white-space: nowrap;
  }
  .title .line-one { top: 0; font-size: 200px; }
  .title .line-two { top: 178px; font-size: 205px; }
  .title .line-three { top: 548px; font-size: 160px; }
  .illustration {
    position: absolute; left: 192px; top: 434px;
    width: 280px; height: 200px;
    z-index: 1;
  }
  .subtitle-lead {
    position: absolute; top: 800px; left: 0; width: 100%;
    text-align: center;
    font-family: "Oswald", sans-serif; font-weight: 600;
    color: var(--ink-white); text-transform: uppercase;
  }
  .subtitle-lead .lead-main { display: block; font-size: 32px; line-height: 1.1; }
  .subtitle-lead .lead-sub { display: block; font-size: 17px; line-height: 1.3; }
  .subtitle-band {
    position: absolute; top: 880px; left: 0; width: 100%; height: 72px;
    background: var(--band-yellow);
    display: flex; align-items: center; justify-content: center;
    text-align: center;
    font-family: "Montserrat", sans-serif; font-weight: 500;
    font-size: 19px; line-height: 1.3;
    color: var(--ink-dark);
  }
</style>
</head>
<body>
  <div class="cover">
    <div class="author">MARLA K. HUGHES</div>

    <h1 class="title">
      <span class="line-one">ROADMAP</span>
      <span class="line-two">TO EARLY</span>
      <span class="line-three">PARENTHOOD</span>
    </h1>

    <svg class="illustration" viewBox="0 0 280 200" role="img"
         aria-label="Flat illustration of a smiling dad carrying a toddler on his shoulders with a young child waving beside him, surrounded by potted plants and floating hearts">
      <defs>
        <linearGradient id="art-tone" x1="0" y1="0" x2="0" y2="1">
          <stop offset="0" stop-color="var(--art-pink)" stop-opacity="0.75"/>
          <stop offset="0.45" stop-color="var(--art-blue)" stop-opacity="0.8"/>
          <stop offset="1" stop-color="var(--art-purple)" stop-opacity="0.8"/>
        </linearGradient>
      </defs>
      <rect x="0" y="0" width="280" height="200" rx="40" fill="url(#art-tone)"/>
    </svg>

    <p class="subtitle-lead">
      <span class="lead-main">Practical Methods for</span>
      <span class="lead-sub">Welcoming a Newborn,</span>
    </p>

    <div class="subtitle-band">
      Juggling Career and Home Life, and Managing Mental Health<br>
      on the Path to Becoming a Parent
    </div>
  </div>
</body>
</html>
```